pathology learning flashcard template graphic design .

Creative designs for 2 sides of the flashcards to include colorful sectioning and font sizes that will make it easy to use in studying.

```html
<!DOCTYPE html>
<html lang="en">
<head>
<meta charset="utf-8">
<title>Pathology Flashcard – Achalasia</title>
<link href="https://fonts.googleapis.com/css2?family=Righteous&family=Alfa+Slab+One&family=Questrial&family=Archivo+Black&family=Fira+Sans+Condensed:wght@600&display=swap" rel="stylesheet">
<style>
  :root{
    --red:#a30000;
    --teal:#2fb8ab;
    --gold:#e5a500;
    --orange:#ff5e1a;
    --ink:#222;
    --paper:#fff;
  }
  *{box-sizing:border-box;margin:0;padding:0}
  html,body{width:899px;height:1200px;overflow:hidden;background:var(--paper)}
  body{position:relative;font-family:"Questrial",sans-serif;color:var(--ink)}
  .card{position:absolute;left:33px;width:831px;border:1.5px solid #333;background:var(--paper)}
  .card--question{top:17px;height:571px}
  .card--answer{top:607px;height:569px}

  .banner{position:absolute;left:0;top:0;width:100%;height:78px;background:var(--gold);
    display:flex;align-items:center;justify-content:center}
  .banner__title{font-family:"Righteous",sans-serif;font-size:54px;line-height:1;color:var(--red);letter-spacing:1px}
  .case-id{position:absolute;left:35px;top:107px;font-size:27px;line-height:1.2;color:var(--red);letter-spacing:-0.5px;font-weight:400}

  .stripe{position:absolute;right:0;width:71px;height:18px}
  .stripe--red{top:93px;background:var(--red)}
  .stripe--teal{top:117px;background:var(--teal)}
  .stripe--gold{top:141px;background:var(--gold)}
  .stripe--orange{top:164px;background:var(--orange)}

  .question-frame{position:absolute;left:15px;top:154px;width:802px;height:404px;
    border:5px solid var(--red);border-radius:38px;background:transparent}
  .question-frame__divider{position:absolute;left:0;right:0;top:309px;height:5px;background:var(--red)}
  .photo-slot{position:absolute;left:19px;top:46px;width:148px;height:212px;border:1px solid var(--red);
    display:flex;align-items:center;justify-content:center;text-align:center;color:var(--red);font-size:19px;line-height:27px}
  .stem{position:absolute;left:185px;top:22px;width:590px;font-size:19.5px;line-height:27.3px;letter-spacing:0.2px}
  .options{position:absolute;left:0;top:318px;width:100%}
  .option{position:absolute;font-size:20px;display:flex;align-items:baseline;gap:16px}
  .option__key{font-family:"Archivo Black",sans-serif;color:var(--red);font-size:20px}
  .option--a{left:98px;top:12px}
  .option--b{left:395px;top:12px}
  .option--c{left:98px;top:47px}
  .option--d{left:395px;top:47px}

  .topic{position:absolute;left:20px;top:10px;font-family:"Alfa Slab One",serif;font-weight:400;font-size:42px;line-height:42px;color:var(--red)}
  .panel{position:absolute;border:5px solid;border-radius:20px;background:var(--paper)}
  .panel__tab{position:absolute;left:4px;top:1px;padding:0 6px;height:29px;border:4px solid;border-top:none;border-left:none;
    font-size:19px;line-height:25px;background:var(--paper)}
  .panel__body{position:absolute;font-size:12.6px;line-height:17.5px}
  .panel--definition{left:14px;top:62px;width:343px;height:136px;border-color:var(--red)}
  .panel--definition .panel__tab{border-color:var(--red);color:var(--red)}
  .panel--etiology{left:14px;top:213px;width:343px;height:137px;border-color:var(--teal)}
  .panel--etiology .panel__tab{border-color:var(--teal);color:var(--teal)}
  .panel--findings{left:371px;top:13px;width:445px;height:337px;border-color:var(--orange)}
  .panel--findings .panel__tab{left:4px;top:1px;height:40px;border-color:var(--orange);color:var(--red);
    font-family:"Fira Sans Condensed",sans-serif;font-weight:600;font-size:23px;line-height:36px;letter-spacing:-0.5px}
  .panel__body p{margin-bottom:10px}
  .label{color:var(--red);font-size:16px}

  .verdict{position:absolute;left:13px;top:365px;width:805px;height:171px;background:var(--gold);border-radius:22px;
    padding:10px 14px 0 14px}
  .verdict__heading{font-size:22px;line-height:1.2;font-weight:400;color:var(--red);display:flex;align-items:baseline;gap:6px}
  .verdict__heading b{font-family:"Archivo Black",sans-serif;font-weight:400;font-size:21px}
  .verdict__text{margin-top:4px;font-size:15.6px;line-height:20.5px;color:#fff}

  .sources{position:absolute;left:14px;top:548px;font-size:9px;font-style:italic;font-family:"Fira Sans Condensed",sans-serif}
  .page-num{position:absolute;left:775px;top:540px;font-size:17px;font-style:italic}
</style>
</head>
<body>

<section class="card card--question">
  <header class="banner"><h1 class="banner__title">GASTROINTESTINAL</h1></header>
  <h2 class="case-id">PATHOLOGY CASE ID 0001</h2>
  <span class="stripe stripe--red"></span>
  <span class="stripe stripe--teal"></span>
  <span class="stripe stripe--gold"></span>
  <span class="stripe stripe--orange"></span>

  <div class="question-frame">
    <div class="photo-slot">INSERT<br>PHOTO<br>HERE</div>
    <p class="stem">50-year-old woman comes to the clinic because she has difficulty swallowing for the past few months. She says symptoms have been worsening. She also complains of cough, mostly at night and in fear of choking, has stopped eating many foods, losing about 12 lbs in the past 3 months. Past medical history is unremarkable. Vital signs are normal and physical exam is unremarkable. Chest x-ray with demonstrates an air-fluid level, while manometry shows absent relaxation of the lower esophageal sphincter during swallowing. What is the most likely diagnosis?</p>
    <div class="question-frame__divider"></div>
    <div class="options">
      <div class="option option--a"><span class="option__key">A)</span>GERD</div>
      <div class="option option--b"><span class="option__key">B)</span>Barret Esophagus</div>
      <div class="option option--c"><span class="option__key">C)</span>Achalasia</div>
      <div class="option option--d"><span class="option__key">D)</span>Eosinophilic esophagitis</div>
    </div>
  </div>
</section>

<section class="card card--answer">
  <h2 class="topic">Achalasia</h2>

  <div class="panel panel--definition">
    <span class="panel__tab">Definition</span>
    <div class="panel__body" style="left:9px;top:40px;width:320px">&bull;Motility disorder where esophageal relaxation is impaired in the lower esophageal sphincter (LES).</div>
  </div>

  <div class="panel panel--etiology">
    <span class="panel__tab">Etiology/Pathology</span>
    <div class="panel__body" style="left:9px;top:42px;width:320px">Destruction of inhibitory neurons in the Auerbach plexus.&nbsp; Loss of peristalsis in the lower esophageal sphincter (Lower-two thirds of the esophagus).</div>
  </div>

  <div class="panel panel--findings">
    <span class="panel__tab">P/E and Symptoms</span>
    <div class="panel__body" style="left:14px;top:57px;width:420px">
      <p>&nbsp;&bull;Dysphagia that is progressive, regurgitation, weight-loss, dry cough, chest pain, GERD, esophageal perforation, squamous cell carcinoma, aspiration pneumonia.</p>
      <p><span class="label">Dx:</span> &bull;Barium swallow will show &lsquo;bird&rsquo;s beak&rsquo; and esophageal dilation.&nbsp; Manometry will present with increased resting lower esophageal sphincter pressure. Endoscopy will usually present with normal mucosa and LES dilation, and in some cases residual material such as undigested food particles may be present.</p>
      <p><span class="label">Rx:</span>&nbsp; First line of treatment are nitrates, calcium channel blockers, and Botulinum toxin injection in the LES.&nbsp; Long term management options include esophageal dilation with pneumatic balloon and myotomy.</p>
    </div>
  </div>

  <div class="verdict">
    <h3 class="verdict__heading"><b>C)</b> Achalasia</h3>
    <p class="verdict__text">Symptoms and studies suggestive of achalasia.&nbsp; Patient&rsquo;s manometry presents with no relaxation of the lower esophageal sphincter during swallowing.&nbsp; Patient also complains of dysphagia and is unable to swallow properly, leading to weight loss.&nbsp; Patient has no past infection or inflammation, ruling out eosinophilic esophagitis.&nbsp; Patient does not have chronic GERD, eliminating the possibility of Barrett esophagus, in which at least 5 years of acid reflux are beforehand to develop columnar metaplasia.</p>
  </div>

  <p class="sources">Sources:Hartwell&rsquo;s Drug Guide;Pocket Pharmacology Companion;Medlibra.net;ClinicaPath.org</p>
  <span class="page-num">1</span>
</section>

</body>
</html>
```